Briloran Clear Springs needs a new business card design (we produce and sell pure bottled water)

We need a clean modern design for our new business cards, We have an existing logo which ultimately cannot be changed, however it could be slighty improved and the colours adjusted. We have this existing logo on all of our bottles, vehicles etc.

Our company slogan is "Clear right to the final sip".
Along with our relevant company information
(Address, phone, website email etc) we will only be using names and not putting position titles for flexibilty.

We are looking for a clean, minimalist modern design.

You can view our website (if need of an update also!) to see our business.

Industry/Entity Type

Business

Contact Information for Business Card

Staff Name : XXXXXX XXXXXX
Address : 9/41 Tavenor St
Halden Rise QLD 4172
Staff Mobile Number : 04XX XXX XXX
Office Phone Number : 07 3918 2457
Staff Email Address : XXXX@brilorancleargo.com.au
Website : www.brilorancleargo.com.au

Font styles to use
Sans Serif

Colors
cee9f5
33a6d7
0492cd
0455a3
3276b5
85abd2
cedeed

Requirements
Must have
• The ability to edit and change the staff members details as we will need to edit for each respective staff member (7 in total)

```html
<!DOCTYPE html>
<html lang="en">
<head>
<meta charset="utf-8">
<title>Briloran Clear Springs – Business Card</title>
<link rel="stylesheet" href="https://fonts.googleapis.com/css2?family=Open+Sans:wght@400;600;700&display=swap">
<style>
  :root {
    --bg: #e9eaec;
    --card-white: #fbfbfb;
    --brand-blue: #1a1aa0;
    --deep-blue: #15159a;
    --text-grey: #2f2f33;
    --faint-water: #d6e6f1;
    --faint-water-edge: #eef4f9;
    --white: #ffffff;
  }
  * { box-sizing: border-box; margin: 0; padding: 0; }
  html, body {
    width: 1200px; height: 844px; overflow: hidden;
    background: var(--bg);
    font-family: "Open Sans", Arial, sans-serif;
  }
  .stage {
    position: relative; width: 1200px; height: 844px;
    display: flex; align-items: center; justify-content: center; gap: 60px;
  }
  .card {
    position: relative; width: 520px; height: 300px;
    box-shadow: 0 6px 18px rgba(0,0,0,0.18);
    overflow: hidden;
  }
  .card--front { background: var(--card-white); }
  .card--back {
    background: var(--deep-blue);
    display: flex; align-items: center; justify-content: center;
  }

  .brand-name {
    font-weight: 700; text-transform: uppercase; line-height: 1.05;
    color: var(--brand-blue);
  }
  .card--front .brand-name {
    position: absolute; top: 36px; right: 28px; width: 180px;
    font-size: 20px; text-align: right;
  }
  .card--back .brand-name {
    color: var(--white); font-size: 36px; text-align: center; width: 320px;
  }

  .product-photo {
    position: absolute; top: 96px; left: 64px; width: 90px; height: 140px;
    border-radius: 14px 14px 8px 8px;
    background: linear-gradient(180deg, var(--faint-water-edge), var(--faint-water));
    opacity: 0.6;
  }
  .staff-name {
    position: absolute; top: 80px; left: 34px;
    font-size: 15px; font-weight: 600; letter-spacing: 0.3px;
    color: var(--brand-blue); text-transform: uppercase;
  }
  .contact {
    position: absolute; top: 140px; left: 64px;
    font-size: 12px; line-height: 20px; color: var(--text-grey);
  }
  .contact .label { color: var(--brand-blue); font-weight: 700; }
  .contact .web { color: var(--brand-blue); font-weight: 700; }
  .contact .gap { margin-left: 8px; }
  .slogan {
    position: absolute; bottom: 30px; left: 64px;
    font-size: 16px; font-weight: 600; letter-spacing: 1.2px;
    color: var(--brand-blue); text-transform: uppercase;
  }
</style>
</head>
<body>
<main class="stage">
  <section class="card card--front">
    <p class="brand-name">Briloran Clear Springs</p>
    <div class="product-photo" role="img" aria-label="Faint photo of a bottled water cooler jug"></div>
    <h1 class="staff-name">Maribel Oakhurst</h1>
    <div class="contact">
      <p><span class="label">P:</span> 0400 587 219 <span class="label gap">M:</span> 07 3918 2457</p>
      <p><span class="label">E:</span> info@brilorancleargo.com.au</p>
      <p class="web">www.brilorancleargo.com.au</p>
      <p>9/41 Tavenor St Halden Rise QLD 4172</p>
    </div>
    <p class="slogan">Clear right to the final sip</p>
  </section>

  <section class="card card--back">
    <p class="brand-name">Briloran Clear Springs</p>
  </section>
</main>
</body>
</html>
```